Plumbing & Heating company

A leaflet containing -

Company name - Larkfield Plumbing Solutions
logo
Mobile number - 07700 914062
Landline - 01632 870215
Email - Info@larkfieldplumbing.example
website - Larkfield-plumbing.example
Social media logos - insta, Facebook

services we offer

- Boiler replacements (free quote)
- General plumbing & heating
- Tap replacements
- 1st & 2nd
- New builds & Extensions
- Cylinder replcemets

```html
<!DOCTYPE html>
<html lang="en">
<head>
<meta charset="utf-8">
<title>Larkfield Plumbing Solutions – Leaflet</title>
<link rel="stylesheet" href="https://fonts.googleapis.com/css2?family=Archivo+Black&family=Poppins:wght@300;400;500;600&family=Oswald:wght@600&display=swap">
<style>
  :root {
    --blue-deep: #0b4f98;
    --blue-mid: #1477c8;
    --dark: #241a1b;
    --orange: #f78a1d;
    --amber: #fbb321;
    --red: #e8333f;
    --white: #ffffff;
    --ink: #141414;
  }
  * { margin: 0; padding: 0; box-sizing: border-box; }
  html, body { width: 991px; height: 1200px; overflow: hidden; background: var(--white); }
  .leaflet { position: relative; width: 991px; height: 1200px; overflow: hidden; font-family: "Poppins", sans-serif; background: var(--white); }

  .hero { position: absolute; left: 0; top: 0; width: 991px; height: 640px;
    background: linear-gradient(160deg, var(--blue-mid) 0%, var(--blue-deep) 60%, #0a4688 100%); }
  .hero-photo { position: absolute; left: 0; top: 0; width: 548px; height: 640px;
    background: linear-gradient(100deg, #d8d4cf 0%, #eceae6 40%, #c9cdd1 70%, #2f7fc6 100%); }

  .brand-box { position: absolute; left: 548px; top: 0; width: 385px; height: 214px; background: var(--dark);
    display: flex; align-items: center; justify-content: center; gap: 10px; }
  .brand-box .mark { width: 22px; height: 22px; border-radius: 50%; background: var(--orange); flex: none; }
  .brand-box .brand-name { font-family: "Archivo Black", sans-serif; color: var(--orange); font-size: 21px; line-height: 1.15; }

  .headline { position: absolute; left: 540px; top: 252px; }
  .headline .big { display: block; font-family: "Archivo Black", sans-serif; font-size: 50px; line-height: 56px;
    color: var(--orange); letter-spacing: -1px; }
  .headline .light { display: block; font-weight: 300; font-size: 43px; line-height: 52px; color: var(--white); letter-spacing: 6px; margin-top: 2px; }
  .accent-bar { position: absolute; left: 542px; top: 443px; width: 47px; height: 5px; background: var(--amber); }
  .intro { position: absolute; left: 540px; top: 470px; width: 300px; color: var(--white); font-size: 16.5px; line-height: 23px; }

  .services { position: absolute; left: 544px; top: 593px; width: 385px; height: 607px; background: var(--dark); color: var(--white); }
  .services h2 { position: absolute; left: 18px; top: 18px; font-family: "Archivo Black", sans-serif; font-size: 24px; color: var(--red); letter-spacing: 0.5px; }
  .service { position: absolute; left: 64px; font-size: 14.5px; font-weight: 500; line-height: 20px; }
  .tick { position: absolute; left: -35px; width: 16px; height: 16px; }
  .free-quote { display: inline-block; margin-top: 6px; background: var(--red); color: var(--white); font-size: 14px; padding: 2px 8px; }
  .divider { position: absolute; left: 64px; width: 308px; border-top: 1px dashed #cfc8c4; }
  .website { position: absolute; left: 16px; top: 457px; font-family: "Oswald", sans-serif; font-weight: 600; font-size: 25px; letter-spacing: 0.5px; }
  .follow { position: absolute; left: 17px; top: 514px; display: flex; align-items: center; gap: 10px; font-size: 15px; letter-spacing: 4px; }
  .social { width: 19px; height: 19px; border-radius: 50%; }
  .social.one { background: #d6336c; margin-left: 4px; }
  .social.two { background: #1877f2; }

  .work-photo { position: absolute; top: 689px; width: 211px; height: 269px; border: 2px solid var(--red); padding: 3px; background: var(--white); }
  .work-photo div { width: 100%; height: 100%; }
  .work-photo.pipes { left: 60px; }
  .work-photo.pipes div { background: linear-gradient(170deg, #b7a58a 0%, #c79a6d 50%, #8f7c63 100%); }
  .work-photo.cupboard { left: 289px; }
  .work-photo.cupboard div { background: linear-gradient(180deg, #caa57d 0%, #d6b38c 60%, #b99670 100%); }

  .contact { position: absolute; left: 60px; top: 990px; }
  .contact h3 { font-family: "Archivo Black", sans-serif; font-size: 23px; line-height: 27px; }
  .contact h3 .red { color: var(--red); display: block; }
  .contact h3 .ink { color: var(--ink); display: block; }
  .contact-line { position: absolute; left: 60px; display: flex; align-items: center; gap: 6px; font-size: 20px; color: var(--ink); white-space: nowrap; }
  .contact-line.phones { top: 1066px; }
  .contact-line.email { top: 1106px; font-weight: 600; font-size: 19.5px; }
  .contact-line .sep { color: var(--red); margin: 0 6px; }
  .contact-line svg { width: 16px; height: 16px; flex: none; }
</style>
</head>
<body>
<main class="leaflet">
  <section class="hero">
    <div class="hero-photo" role="img" aria-label="Photo of an installed hot water cylinder and wall-hung boiler with copper pipework"></div>
    <div class="brand-box">
      <span class="mark"></span>
      <span class="brand-name">LARKFIELD<br>PLUMBING SOLUTIONS</span>
    </div>
    <h1 class="headline">
      <span class="big">LARKFIELD</span>
      <span class="big">PLUMBING</span>
      <span class="light">SOLUTIONS</span>
    </h1>
    <div class="accent-bar"></div>
    <p class="intro">Larkfield Plumbing &amp; Heating contractor based in Westvale and covering Hollowmere and the surrounding areas.</p>
  </section>

  <div class="work-photo pipes"><div role="img" aria-label="Photo of first fix copper pipework laid between floor joists"></div></div>
  <div class="work-photo cupboard"><div role="img" aria-label="Photo of a boiler and pipework installed in a plywood cupboard"></div></div>

  <section class="contact">
    <h3><span class="red">CONTACT US FOR</span><span class="ink">MORE INFORMATION</span></h3>
  </section>
  <div class="contact-line phones">
    <svg viewBox="0 0 16 16"><path d="M3 1.5l3 .5 1 3.5-2 1.2a8 8 0 0 0 4.3 4.3l1.2-2 3.5 1 .5 3c-.5 1-1.5 1.5-2.5 1.5C6.5 14.5 1.5 9.5 1.5 4 1.5 3 2 2 3 1.5z" fill="var(--orange)"/></svg>
    <span>07700 914062</span><span class="sep">|</span>
    <svg viewBox="0 0 16 16"><path d="M1 6c2-3 12-3 14 0l-2 2-2-1V5.5H5V7L3 8z M4 8h8l2 6H2z" fill="var(--orange)"/><circle cx="8" cy="11" r="1.6" fill="#fff"/></svg>
    <span>01632 870215</span>
  </div>
  <div class="contact-line email">
    <svg viewBox="0 0 16 16"><circle cx="8" cy="8" r="8" fill="var(--amber)"/><rect x="4" y="5" width="8" height="6" fill="#fff"/><path d="M4 5l4 3.5L12 5" stroke="var(--amber)" fill="none"/></svg>
    <span>Info@larkfieldplumbing.example</span>
  </div>

  <section class="services">
    <h2>SERVICES WE OFFER</h2>
    <div class="service" style="top:74px"><svg class="tick" style="top:22px" viewBox="0 0 16 16"><circle cx="8" cy="8" r="8" fill="var(--amber)"/><path d="M4.5 8.2l2.3 2.3 4.7-4.7" stroke="var(--dark)" stroke-width="1.8" fill="none"/></svg>Boiler replacements<br><span class="free-quote">FREE QUOTE</span></div>
    <div class="divider" style="top:150px"></div>
    <div class="service" style="top:163px"><svg class="tick" style="top:2px" viewBox="0 0 16 16"><circle cx="8" cy="8" r="8" fill="var(--amber)"/><path d="M4.5 8.2l2.3 2.3 4.7-4.7" stroke="var(--dark)" stroke-width="1.8" fill="none"/></svg>General plumbing &amp; heating</div>
    <div class="divider" style="top:203px"></div>
    <div class="service" style="top:221px"><svg class="tick" style="top:2px" viewBox="0 0 16 16"><circle cx="8" cy="8" r="8" fill="var(--amber)"/><path d="M4.5 8.2l2.3 2.3 4.7-4.7" stroke="var(--dark)" stroke-width="1.8" fill="none"/></svg>Tap replacements</div>
    <div class="divider" style="top:258px"></div>
    <div class="service" style="top:278px"><svg class="tick" style="top:2px" viewBox="0 0 16 16"><circle cx="8" cy="8" r="8" fill="var(--amber)"/><path d="M4.5 8.2l2.3 2.3 4.7-4.7" stroke="var(--dark)" stroke-width="1.8" fill="none"/></svg>System design &amp; installation<br>1st &amp; 2nd fix</div>
    <div class="divider" style="top:337px"></div>
    <div class="service" style="top:356px"><svg class="tick" style="top:2px" viewBox="0 0 16 16"><circle cx="8" cy="8" r="8" fill="var(--amber)"/><path d="M4.5 8.2l2.3 2.3 4.7-4.7" stroke="var(--dark)" stroke-width="1.8" fill="none"/></svg>New builds &amp; Extensions</div>
    <div class="divider" style="top:394px"></div>
    <div class="service" style="top:413px"><svg class="tick" style="top:2px" viewBox="0 0 16 16"><circle cx="8" cy="8" r="8" fill="var(--amber)"/><path d="M4.5 8.2l2.3 2.3 4.7-4.7" stroke="var(--dark)" stroke-width="1.8" fill="none"/></svg>Cylinder replcemets</div>
    <div class="website">Larkfield-plumbing.example</div>
    <div class="follow">FOLLOW US ON <span class="social one"></span><span class="social two"></span></div>
  </section>
</main>
</body>
</html>
```